BOLD & MINIMALIST DESIGN NEEDED

We want a very bold but minimalistic business card design that is impactful and utilizes both sides of the business card. Our current logo is included for your use.

We want bold fonts and good use of negative space. We don't want the logo to overpower the design.

Target Market(s)

Professionals who are building new commercial buildings.

Industry/Entity Type

Construction

Contact Information for Business Card

Name, Title, email, office phone, cell phone, website

Font styles to use
Serif
Sans Serif

Requirements
Must have
• Bold design!

```html
<!DOCTYPE html>
<html lang="en">
<head>
<meta charset="utf-8">
<title>Crestline Design + Build — Business Card</title>
<link rel="stylesheet" href="https://fonts.googleapis.com/css2?family=Montserrat:wght@400;500;800&display=swap">
<style>
  :root {
    --bg: #3a3a3a;
    --green: #86c342;
    --black: #0d0d0d;
    --white: #ffffff;
    --card-w: 540px;
    --card-h: 310px;
    --radius: 22px;
  }
  * { box-sizing: border-box; margin: 0; padding: 0; }
  html, body {
    width: 1200px; height: 689px; overflow: hidden;
    background: var(--bg);
    font-family: "Montserrat", Arial, sans-serif;
  }
  .stage {
    width: 1200px; height: 689px;
    display: flex; align-items: center; justify-content: center; gap: 40px;
  }
  .card {
    position: relative;
    width: var(--card-w); height: var(--card-h);
    border-radius: var(--radius);
    overflow: hidden;
  }

  /* Front */
  .card-front {
    background: var(--green);
    display: flex; flex-direction: column; align-items: center; justify-content: center;
    color: var(--white);
  }
  .front-mark { display: flex; align-items: center; gap: 14px; }
  .front-mark .dot { width: 44px; height: 44px; background: var(--white); }
  .front-name { font-weight: 800; font-size: 52px; letter-spacing: 1px; line-height: 1; }
  .front-tagline {
    margin-top: 12px; padding-top: 8px;
    border-top: 2px solid var(--white);
    font-weight: 800; font-size: 18px; letter-spacing: 11px;
  }

  /* Back */
  .card-back { background: var(--white); }
  .card-back .wave { position: absolute; inset: 0; width: 100%; height: 100%; }
  .back-brand {
    position: absolute; top: 22px; right: 34px;
    text-align: right; color: var(--black);
  }
  .back-brand .name { font-weight: 800; font-size: 30px; line-height: 1; letter-spacing: .5px; }
  .back-brand .tagline {
    font-weight: 800; font-size: 10px; letter-spacing: 6px; margin-top: 5px;
    border-top: 1.5px solid var(--black); padding-top: 4px;
  }
  .person { position: absolute; left: 34px; top: 176px; color: var(--white); }
  .person .full-name {
    color: var(--green); font-weight: 800; font-size: 22px; line-height: 26px; letter-spacing: .5px;
  }
  .person .role { font-weight: 500; font-size: 12px; line-height: 15px; letter-spacing: .5px; }
  .contact-list { list-style: none; margin-top: 8px; }
  .contact-list li {
    display: flex; align-items: center; gap: 9px;
    font-size: 12px; font-weight: 400; line-height: 18px;
  }
  .contact-list svg { width: 11px; height: 11px; fill: var(--green); flex: none; }
  .address {
    position: absolute; right: 34px; bottom: 40px;
    color: var(--white); font-size: 12px; line-height: 18px; text-align: right;
  }
</style>
</head>
<body>
<main class="stage">

  <section class="card card-front" aria-label="Card front">
    <div class="front-mark">
      <span class="dot" aria-hidden="true"></span>
      <span class="front-name">CRESTLINE</span>
    </div>
    <div class="front-tagline">DESIGN + BUILD</div>
  </section>

  <section class="card card-back" aria-label="Card back">
    <svg class="wave" viewBox="0 0 540 310" preserveAspectRatio="none" aria-hidden="true">
      <path fill="none" stroke="var(--green)" stroke-width="6" stroke-linecap="round"
            d="M40,152 C110,128 220,122 330,114 C430,108 505,90 548,52"/>
      <path fill="var(--black)"
            d="M0,310 L0,168 C100,140 220,135 330,128 C430,122 510,104 540,72 L540,310 Z"/>
    </svg>

    <div class="back-brand">
      <div class="name">CRESTLINE</div>
      <div class="tagline">DESIGN + BUILD</div>
    </div>

    <div class="person">
      <div class="full-name">MARCUS VALE</div>
      <div class="role">OWNER-CEO</div>
      <ul class="contact-list">
        <li><svg viewBox="0 0 24 24"><path d="M6.6 10.8a15 15 0 0 0 6.6 6.6l2.2-2.2a1 1 0 0 1 1-.25 11.4 11.4 0 0 0 3.6.57 1 1 0 0 1 1 1V20a1 1 0 0 1-1 1A17 17 0 0 1 3 4a1 1 0 0 1 1-1h3.5a1 1 0 0 1 1 1c0 1.25.2 2.45.57 3.57a1 1 0 0 1-.25 1z"/></svg>123 456 789</li>
        <li><svg viewBox="0 0 24 24"><path d="M7 1h10a2 2 0 0 1 2 2v18a2 2 0 0 1-2 2H7a2 2 0 0 1-2-2V3a2 2 0 0 1 2-2zm0 3v14h10V4zm5 15.5a1 1 0 1 0 0 2 1 1 0 0 0 0-2z"/></svg>123 456 789</li>
        <li><svg viewBox="0 0 24 24"><path d="M2 5h20v14H2zm2 2v.5l8 5 8-5V7l-8 5z"/></svg>info@crestlinebuild.com</li>
        <li><svg viewBox="0 0 24 24"><circle cx="12" cy="12" r="10"/></svg>www.crestlinebuild.com</li>
      </ul>
    </div>

    <div class="address">Your address, City<br>State, Zip 1234</div>
  </section>

</main>
</body>
</html>
```